Event Center Website

We need a new website design for an upscale event center in Reno, Nevada. The building hosts everything from weddings to corporate events to funerals and it competitively more expensive. The overall look and feel is consistent with a Lake Tahoe aesthetic. The current site can be viewed at www.themaplehallevents.com. They are looking for a major upgrade. A sample site they like is www.cliffsidelodgestay.com. We have new photography available (some attached). The site should be very visual. A site map is attached as well for direction on what elements the site should include as well as labels for navigation. I am looking for a home page and sample interior page. Any questions, let me know. Thanks.
Updates

I have added some photography of the center itself for use rather than stock photography. Thanks!

Target Market(s)

Brides, professionals, high-income

Industry/Entity Type

Building

Requirements
Must have
• See site map

```html
<!DOCTYPE html>
<html lang="en">
<head>
<meta charset="utf-8">
<title>Maple Hall at Cedar Ridge — Gallery</title>
<link href="https://fonts.googleapis.com/css2?family=PT+Sans+Narrow:wght@400;700&family=PT+Sans:wght@400&display=swap" rel="stylesheet">
<style>
:root{
  --brown:#5b2f16;
  --brown-dark:#3d1d0c;
  --text:#4a2a16;
  --cream:#f4f0e4;
  --white:#ffffff;
  --line:#ddd6c6;
  --footer:#1f0a04;
  --footer-text:#b9aa98;
}
*{margin:0;padding:0;box-sizing:border-box}
html,body{width:1192px;height:1200px;overflow:hidden}
body{background:var(--cream);font-family:"PT Sans Narrow",sans-serif;color:var(--text);position:relative}
.site-header{position:absolute;left:0;top:0;width:1192px;height:101px;background:var(--white)}
.brand{position:absolute;left:97px;top:27px;height:56px;display:flex;align-items:center;gap:8px}
.brand-mark{width:14px;height:14px;background:var(--brown)}
.brand-name{font-size:24px;color:var(--brown);font-weight:700;letter-spacing:.3px}
.main-nav{position:absolute;left:334px;top:46px;width:762px;display:flex;justify-content:space-between}
.main-nav a{font-size:13px;color:var(--brown-dark);text-decoration:none;text-transform:uppercase}
.hero{position:absolute;left:0;top:101px;width:1192px;height:234px;
  background:linear-gradient(180deg,#3d2e26 0%,#5a4537 40%,#4f6a32 72%,#46342a 100%)}
.booking{position:absolute;left:98px;top:274px;width:996px;height:94px;background:var(--white);
  border-radius:3px;box-shadow:0 10px 14px -8px rgba(0,0,0,.35);display:flex;align-items:center;padding:0 18px 0 14px}
.booking h2{font-weight:400;font-size:21px;color:var(--brown-dark);width:201px}
.field{width:181px;height:42px;border:1px solid #c9b9ae;border-radius:2px;margin-right:15px;
  display:flex;align-items:center;justify-content:space-between;padding:0 12px;font-family:"PT Sans",sans-serif;font-size:13px;color:#7a6e66}
.field:nth-of-type(3){margin-right:8px}
.btn-reserve{width:180px;height:42px;border:0;border-radius:2px;background:linear-gradient(#6e3a1c,#552a12);
  color:var(--white);font-family:"PT Sans Narrow",sans-serif;font-size:16px}
.section-title{position:absolute;left:0;top:390px;width:1192px;text-align:center;font-size:27px;font-weight:700;color:var(--brown)}
.divider{position:absolute;left:98px;top:444px;width:996px;height:8px}
.gallery-card{position:absolute;width:312px;height:291px;background:var(--white);border:1px solid #ece6d8;padding:8px}
.gallery-photo{width:294px;height:233px}
.gallery-caption{display:flex;justify-content:space-between;align-items:center;height:42px;padding:0 10px 0 8px;
  font-size:15px;text-transform:uppercase;color:var(--brown-dark)}
.site-footer{position:absolute;left:0;top:1137px;width:1192px;height:63px;background:var(--footer)}
.copyright{position:absolute;left:98px;top:24px;font-size:12px;color:var(--footer-text)}
.social{position:absolute;left:514px;top:16px;display:flex;gap:5px}
.social span{width:29px;height:29px;border:1.5px solid var(--footer-text);border-radius:50%;display:flex;align-items:center;justify-content:center}
.social span::after{content:"";width:8px;height:8px;border-radius:50%;background:var(--footer-text)}
.legal{position:absolute;right:98px;top:24px;font-size:12px;color:var(--footer-text);text-transform:uppercase}
</style>
</head>
<body>
<header class="site-header">
  <div class="brand"><span class="brand-mark"></span><span class="brand-name">Maple Hall</span></div>
  <nav class="main-nav">
    <a href="#">About Us</a><a href="#">Gallery</a><a href="#">Weddings</a><a href="#">Meetings</a>
    <a href="#">Other Events</a><a href="#">Catering</a><a href="#">Menus</a><a href="#">FAQs</a>
    <a href="#">Testimonials</a><a href="#">Contact</a>
  </nav>
</header>

<div class="hero" role="img" aria-label="Event hall interior with draped ceiling, chandelier and tall windows onto trees"></div>

<form class="booking">
  <h2>Schedule an Appointment</h2>
  <div class="field">Arrival Date<svg width="11" height="11" viewBox="0 0 11 11"><rect x=".5" y="1.5" width="10" height="9" fill="none" stroke="#888"/><path d="M.5 4h10M3 0v3M8 0v3" stroke="#888"/></svg></div>
  <div class="field">Departure Date<svg width="11" height="11" viewBox="0 0 11 11"><rect x=".5" y="1.5" width="10" height="9" fill="none" stroke="#888"/><path d="M.5 4h10M3 0v3M8 0v3" stroke="#888"/></svg></div>
  <div class="field">Adults<svg width="11" height="11" viewBox="0 0 11 11"><rect x=".5" y="1.5" width="10" height="9" fill="none" stroke="#888"/><path d="M.5 4h10M3 0v3M8 0v3" stroke="#888"/></svg></div>
  <button class="btn-reserve" type="button">RESERVE Online</button>
</form>

<h1 class="section-title">OUR GALLERY</h1>
<svg class="divider" viewBox="0 0 996 8"><path d="M0 4h497M515 4h481" stroke="var(--line)" stroke-width="2" stroke-dasharray="1 1"/><rect x="500" y="1" width="12" height="6" rx="3" fill="none" stroke="#c9bfae"/></svg>

<div class="gallery-card" style="left:97px;top:480px"><div class="gallery-photo" role="img" aria-label="Ceremony hall with draped ceiling and rows of white chairs" style="background:linear-gradient(#7a5a3c,#4a3a30 60%,#b9aea6)"></div><div class="gallery-caption">Holiday or Seasonal Parties<span>»</span></div></div>
<div class="gallery-card" style="left:440px;top:480px"><div class="gallery-photo" role="img" aria-label="Sweetheart table under a floral arch with pink drapery" style="background:linear-gradient(#b48a8c,#7d8d5a 45%,#9c8772)"></div><div class="gallery-caption">Holiday or Seasonal Parties<span>»</span></div></div>
<div class="gallery-card" style="left:783px;top:480px"><div class="gallery-photo" role="img" aria-label="Lounge opening onto a garden patio" style="background:linear-gradient(#6a4c38,#8a8660 45%,#4e423c)"></div><div class="gallery-caption">Holiday or Seasonal Parties<span>»</span></div></div>
<div class="gallery-card" style="left:97px;top:803px"><div class="gallery-photo" role="img" aria-label="Close view of a rose and greenery floral arrangement" style="background:linear-gradient(#a47a74,#8f9070 50%,#d6d3c6)"></div><div class="gallery-caption">Holiday or Seasonal Parties<span>»</span></div></div>
<div class="gallery-card" style="left:440px;top:803px"><div class="gallery-photo" role="img" aria-label="Lodge-style building exterior under a blue sky" style="background:linear-gradient(#2f66aa,#6a5c4e 45%,#8a6a4c)"></div><div class="gallery-caption">Holiday or Seasonal Parties<span>»</span></div></div>
<div class="gallery-card" style="left:783px;top:803px"><div class="gallery-photo" role="img" aria-label="Candlelit dining room with stone fireplace and flowers" style="background:linear-gradient(#8e6238,#bb8848 55%,#5a3a22)"></div><div class="gallery-caption">Holiday or Seasonal Parties<span>»</span></div></div>

<footer class="site-footer">
  <p class="copyright">©2013 - 2014&nbsp; Maple Hall at Cedar Ridge , All Rights Reserved.</p>
  <div class="social" aria-label="Social links"><span></span><span></span><span></span><span></span><span></span></div>
  <p class="legal">Privacy Policy&nbsp; / &nbsp;Careers</p>
</footer>
</body>
</html>
```